BuildLinkHub.com Full Stationery Design

Business Card will have all info on it. Letterhead will not have name, title or mobile number. Keep general feeling very clean, using colors from the logo as accents.
Name:Dale Marchetti
Title:President
Phone: 1-800-555-0142
Cell: 306-555-0187
email: dale@buildlinkhub.example
website: www.buildlinkhub.example
Address:
PO Box 947
Alderton, MB
S0J2T0

Target Market(s)

Construction Business owners

Industry/Entity Type

Business

Contact Information for Business Card

Name:Dale Marchetti
Title:President
Phone: 1-800-555-0142
Cell: 306-555-0187
Address:
PO Box 947
Alderton, MB
S0J2T0

Font styles to use
Sans Serif

Requirements
Must have
• Clean look
Should not have
• Images or cartoon type characters or tools

```html
<!DOCTYPE html>
<html lang="en">
<head>
<meta charset="utf-8">
<title>BuildLinkHub.com – Business Card</title>
<link rel="stylesheet" href="https://fonts.googleapis.com/css2?family=Montserrat:wght@600&family=Merriweather:wght@700&family=Roboto:wght@400&display=swap">
<style>
  :root {
    --bg: #fba865;
    --orange-deep: #e2291f;
    --orange: #ee6a0c;
    --orange-text: #e8521a;
    --slate: #4a5360;
    --grey: #6f747b;
    --rule: #b9bdc3;
    --white: #ffffff;
    --edge-grey: #8d949d;
  }
  * { margin: 0; padding: 0; box-sizing: border-box; }
  html, body { width: 1200px; height: 856px; overflow: hidden; }
  body {
    background: var(--bg);
    position: relative;
    font-family: "Roboto", Arial, sans-serif;
  }
  .card {
    position: absolute;
    width: 525px;
    height: 300px;
    border-radius: 28px;
    overflow: hidden;
    box-shadow: 0 14px 30px rgba(160, 70, 10, 0.25);
  }
  .brand {
    font-family: "Montserrat", Arial, sans-serif;
    font-weight: 600;
    letter-spacing: 0.5px;
    display: flex;
    align-items: center;
    white-space: nowrap;
  }
  .brand-mark { flex: none; }

  /* Back of card */
  .card-back {
    left: 620px;
    top: 110px;
    background: linear-gradient(160deg, var(--orange-deep) 0%, var(--orange) 60%);
    display: flex;
    align-items: center;
    justify-content: center;
  }
  .card-back .brand { color: var(--white); font-size: 30px; gap: 14px; }
  .card-back .brand-mark { background: var(--white); width: 34px; height: 34px; }

  /* Front of card */
  .card-front {
    left: 60px;
    top: 450px;
    background: var(--white);
  }
  .card-front .brand-area {
    position: absolute;
    left: 30px;
    top: 0;
    width: 255px;
    height: 100%;
    display: flex;
    align-items: center;
  }
  .card-front .brand { color: var(--slate); font-size: 21px; gap: 12px; }
  .card-front .brand-mark { background: var(--orange-text); width: 26px; height: 26px; }
  .divider {
    position: absolute;
    left: 300px;
    top: 60px;
    width: 1px;
    height: 150px;
    background: var(--rule);
  }
  .contact {
    position: absolute;
    left: 322px;
    top: 56px;
  }
  .contact-name {
    font-family: "Merriweather", Georgia, serif;
    font-weight: 700;
    color: var(--orange-text);
    font-size: 17px;
    line-height: 1.1;
  }
  .contact-title {
    font-family: "Merriweather", Georgia, serif;
    font-weight: 700;
    color: var(--grey);
    font-size: 10.5px;
    margin-bottom: 8px;
  }
  .contact-list { list-style: none; }
  .contact-list li {
    display: flex;
    align-items: center;
    gap: 7px;
    font-size: 11px;
    color: var(--grey);
    line-height: 18px;
    white-space: nowrap;
  }
  .contact-icon { width: 11px; height: 11px; flex: none; }
  .edge-band {
    position: absolute;
    left: 0;
    bottom: 0;
    width: 100%;
    height: 10px;
    display: flex;
  }
  .edge-band-accent { flex: 7; background: linear-gradient(90deg, var(--orange-deep), var(--orange)); }
  .edge-band-neutral { flex: 3; background: var(--edge-grey); }
</style>
</head>
<body>

<section class="card card-back" aria-label="Business card back">
  <div class="brand"><span class="brand-mark"></span>BuildLinkHub.com</div>
</section>

<section class="card card-front" aria-label="Business card front">
  <div class="brand-area">
    <div class="brand"><span class="brand-mark"></span>BuildLinkHub.com</div>
  </div>
  <div class="divider"></div>
  <div class="contact">
    <p class="contact-name">Dale Marchetti</p>
    <p class="contact-title">President</p>
    <ul class="contact-list">
      <li>
        <svg class="contact-icon" viewBox="0 0 12 12" aria-hidden="true"><path d="M6 1a3.5 3.5 0 0 0-3.5 3.5C2.5 7 6 11 6 11s3.5-4 3.5-6.5A3.5 3.5 0 0 0 6 1z" fill="#e8521a"/><circle cx="6" cy="4.5" r="1.3" fill="#fff"/></svg>
        PO Box 947, Alderton, MB, S0J2T0
      </li>
      <li>
        <svg class="contact-icon" viewBox="0 0 12 12" aria-hidden="true"><circle cx="6" cy="6" r="5.5" fill="#e8521a"/><path d="M3.5 4.5l1-1 1.2 1.2-.7.7c.4.8 1 1.4 1.8 1.8l.7-.7 1.2 1.2-1 1C5.8 8.6 3.6 6.4 3.5 4.5z" fill="#fff"/></svg>
        1-800-555-0142
      </li>
      <li>
        <svg class="contact-icon" viewBox="0 0 12 12" aria-hidden="true"><path d="M2 2.5l2-1 1.6 2.4-1.2 1c.6 1.2 1.5 2.1 2.7 2.7l1-1.2L10.5 8l-1 2C5.5 10 2 6.5 2 2.5z" fill="#e8521a"/></svg>
        306-555-0187
      </li>
      <li>
        <svg class="contact-icon" viewBox="0 0 12 12" aria-hidden="true"><rect x="1" y="2.5" width="10" height="7" rx="1" fill="#e8521a"/><path d="M1.5 3.2L6 6.5l4.5-3.3" stroke="#fff" fill="none" stroke-width="1"/></svg>
        dale@buildlinkhub.example
      </li>
      <li>
        <svg class="contact-icon" viewBox="0 0 12 12" aria-hidden="true"><circle cx="6" cy="6" r="5" fill="#e8521a"/><path d="M1 6h10M6 1c-2 2.5-2 7.5 0 10M6 1c2 2.5 2 7.5 0 10" stroke="#fff" fill="none" stroke-width="0.8"/></svg>
        www.buildlinkhub.example
      </li>
    </ul>
  </div>
  <div class="edge-band"><span class="edge-band-accent"></span><span class="edge-band-neutral"></span></div>
</section>

</body>
</html>
```